Garlic Farm for Farm Sales/Restaurant sales

Need a professional, but appealing to agriculture world. We are selling 27 kinds of Organic Garlic from a farm in Simla,CO. I have uploaded logo and business information-we are going to need a template, because I will need to use it for four separate people.
-We are trying to appeal to Farm to table restaurants
-As well as growers/farmers

Target Market(s)

Agriculture Sales/Restaurants-Organic

Industry/Entity Type

Agriculture

Contact Information for Business Card

Want it to look more unique then your average kelto stock card- I want it to look amazing

Font styles to use
Sans Serif

Colors
0455a3
ec1f27
fbed22
ffffff

Requirements
Must have
• Just be creative
Nice to have
• Colorful
Should not have
• plain

```html
<!DOCTYPE html>
<html lang="en">
<head>
<meta charset="utf-8">
<title>Ridgeline Garlic – Business Card</title>
<link href="https://fonts.googleapis.com/css2?family=Open+Sans:wght@400;600;700&display=swap" rel="stylesheet">
<style>
  :root {
    --brand-blue: #0455a3;
    --brand-red: #ec1f27;
    --brand-yellow: #fbed22;
    --card-yellow: #fcd20f;
    --paper: #ffffff;
    --backdrop: #e9e9e9;
    --card-shadow: rgba(0, 0, 0, 0.12);
  }
  * { box-sizing: border-box; margin: 0; padding: 0; }
  html, body {
    width: 1200px;
    height: 900px;
    overflow: hidden;
    background: var(--backdrop);
    font-family: "Open Sans", Arial, sans-serif;
  }
  .canvas {
    position: relative;
    width: 1200px;
    height: 900px;
    display: flex;
    align-items: center;
    justify-content: center;
    gap: 50px;
  }
  .card {
    position: relative;
    width: 500px;
    height: 286px;
    box-shadow: 0 6px 18px var(--card-shadow);
  }
  .card--front { background: var(--paper); }
  .card--back {
    background: var(--card-yellow);
    display: flex;
    align-items: center;
    justify-content: center;
  }

  .contact-person {
    position: absolute;
    left: 34px;
    top: 30px;
  }
  .contact-person__name {
    color: var(--brand-red);
    font-weight: 700;
    font-size: 22px;
    line-height: 1.1;
  }
  .contact-person__role {
    color: var(--brand-blue);
    font-size: 14px;
    margin-top: 2px;
  }

  .contact-list {
    position: absolute;
    left: 34px;
    top: 100px;
    list-style: none;
  }
  .contact-list__item {
    display: flex;
    align-items: center;
    gap: 8px;
    color: var(--brand-blue);
    font-size: 12px;
    line-height: 18px;
  }
  .contact-list__icon {
    width: 11px;
    height: 11px;
    flex: none;
  }
  .contact-address {
    position: absolute;
    left: 34px;
    top: 186px;
    color: var(--brand-blue);
    font-size: 12px;
    line-height: 17px;
    font-style: normal;
  }

  .brand-mark {
    display: flex;
    align-items: center;
    gap: 10px;
  }
  .brand-mark__dot {
    width: 44px;
    height: 44px;
    border-radius: 50%;
    background: var(--brand-red);
    flex: none;
  }
  .brand-mark__name {
    color: var(--brand-blue);
    font-weight: 700;
    font-size: 28px;
    line-height: 1;
    letter-spacing: 0.2px;
  }
  .card--front .brand-mark {
    position: absolute;
    right: 30px;
    bottom: 36px;
  }
  .card--back .brand-mark__dot { width: 52px; height: 52px; }
  .card--back .brand-mark__name { font-size: 34px; }
</style>
</head>
<body>
<main class="canvas">

  <section class="card card--front" aria-label="Business card front">
    <header class="contact-person">
      <h1 class="contact-person__name">dana whitfield</h1>
      <p class="contact-person__role">Owner</p>
    </header>

    <ul class="contact-list">
      <li class="contact-list__item">
        <svg class="contact-list__icon" viewBox="0 0 12 12" aria-hidden="true">
          <rect width="12" height="12" rx="2" fill="var(--brand-red)"/>
          <path d="M3.5 2.5h2l.5 2-1 .8a5 5 0 0 0 1.7 1.7l.8-1 2 .5v2c-3.5.3-6.3-2.5-6-6z" fill="#fff"/>
        </svg>
        555.014.2280
      </li>
      <li class="contact-list__item">
        <svg class="contact-list__icon" viewBox="0 0 12 12" aria-hidden="true">
          <rect width="12" height="12" rx="2" fill="var(--brand-red)"/>
          <rect x="4" y="2" width="4" height="8" rx="0.8" fill="#fff"/>
        </svg>
        555.014.7731
      </li>
      <li class="contact-list__item">
        <svg class="contact-list__icon" viewBox="0 0 12 12" aria-hidden="true">
          <rect width="12" height="12" rx="2" fill="var(--brand-red)"/>
          <rect x="2.5" y="3.5" width="7" height="5" fill="#fff"/>
          <path d="M2.5 3.5 6 6.5l3.5-3" fill="none" stroke="var(--brand-red)" stroke-width="0.8"/>
        </svg>
        hello@ridgeline.farm
      </li>
      <li class="contact-list__item">
        <svg class="contact-list__icon" viewBox="0 0 12 12" aria-hidden="true">
          <circle cx="6" cy="6" r="6" fill="var(--brand-red)"/>
          <circle cx="6" cy="6" r="3.5" fill="none" stroke="#fff" stroke-width="0.9"/>
          <path d="M2.5 6h7M6 2.5v7" stroke="#fff" stroke-width="0.9"/>
        </svg>
        www.ridgeline.farm
      </li>
    </ul>

    <address class="contact-address">
      PO Box 2210,<br>
      Simla, CO 80835
    </address>

    <div class="brand-mark">
      <span class="brand-mark__dot" aria-hidden="true"></span>
      <span class="brand-mark__name">ridgeline garlic</span>
    </div>
  </section>

  <section class="card card--back" aria-label="Business card back">
    <div class="brand-mark">
      <span class="brand-mark__dot" aria-hidden="true"></span>
      <span class="brand-mark__name">ridgeline garlic</span>
    </div>
  </section>

</main>
</body>
</html>
```